Commercial Loan Originator Business Card (CHANGE COLORS SCHEME)

CHANGE COLOR SCHEME - SAME DESIGN

Name Marlene Agate
Title Commercial Loan Originator
Office (800) 417-2906 x68
Direct (240) 615-2043
Email freshgreens4life@quillbox.example

Name Dale Morrow
Office (800) 417-2906 x70
Direct (410) 392-5184
Email d.morthehomeguy@quillbox.example

Name Leonard Vasko
Office (800) 417-2906 x71
Direct (215) 463-0712
Email l.vasko41@quillbox.example

Name Gwen Halsey
Office (800) 417-2906 x
Direct (202) 548-1370
Email ghalsey63@quillbox.example

Name Mirna Ashby
Office (800) 417-2906 x72
Direct (240) 871-4526
Email tristatehomelending@quillbox.example

```html
<!DOCTYPE html>
<html lang="en">
<head>
<meta charset="UTF-8">
<title>Marlene Agate – Business Card</title>
<link rel="stylesheet" href="https://fonts.googleapis.com/css2?family=Cinzel:wght@400;500&family=Montserrat:wght@400;500;600&display=swap">
<style>
  :root {
    --brand-green: #1e6b58;
    --brand-green-light: #3f9a80;
    --card-white: #fbfbf8;
    --front-text: #f3eedf;
    --body-grey: #5f6662;
    --rule-tone: #9fb3ab;
    --backdrop: #e6e6e6;
    --photo-light: #eef1ef;
  }
  * { margin: 0; padding: 0; box-sizing: border-box; }
  html, body { width: 1200px; height: 800px; overflow: hidden; }
  body {
    background: var(--backdrop);
    font-family: "Montserrat", Arial, sans-serif;
    position: relative;
  }
  .card {
    position: absolute;
    left: 320px;
    width: 560px;
    height: 320px;
    box-shadow: 0 10px 28px rgba(0,0,0,0.18);
  }
  .card--front {
    top: 50px;
    background: var(--brand-green);
    display: flex;
    flex-direction: column;
    align-items: center;
    justify-content: center;
    color: var(--front-text);
  }
  .front-name {
    font-family: "Cinzel", Georgia, serif;
    font-weight: 400;
    font-size: 46px;
    letter-spacing: 1px;
    line-height: 1;
  }
  .front-title {
    margin-top: 8px;
    font-size: 21px;
    letter-spacing: 3.5px;
    font-weight: 400;
  }
  .card--back {
    top: 430px;
    background: var(--card-white);
  }
  .back-identity {
    position: absolute;
    left: 44px;
    right: 70px;
    top: 140px;
  }
  .back-name {
    color: var(--brand-green);
    font-weight: 600;
    font-size: 21px;
    text-transform: uppercase;
    letter-spacing: 0.3px;
    line-height: 1.1;
  }
  .title-row {
    display: flex;
    align-items: flex-end;
    gap: 14px;
    margin-top: 2px;
  }
  .back-title {
    color: var(--body-grey);
    font-size: 15px;
    letter-spacing: 0.8px;
    white-space: nowrap;
    line-height: 20px;
  }
  .title-rule {
    flex: 1;
    height: 1px;
    margin-bottom: 5px;
    background: var(--rule-tone);
  }
  .contact-list {
    position: absolute;
    left: 44px;
    top: 196px;
    list-style: none;
  }
  .contact-item {
    display: flex;
    align-items: center;
    gap: 8px;
    color: var(--body-grey);
    font-size: 14.5px;
    line-height: 24px;
  }
  .contact-icon { width: 15px; height: 15px; flex: none; }
  .contact-icon path { fill: var(--brand-green); }
  .portrait {
    position: absolute;
    left: 378px;
    top: 18px;
    width: 112px;
    height: 112px;
    border-radius: 50%;
    border: 6px solid var(--brand-green);
    padding: 5px;
    background: var(--card-white);
  }
  .portrait-fill {
    width: 100%;
    height: 100%;
    border-radius: 50%;
    background: linear-gradient(180deg, var(--photo-light) 0%, var(--photo-light) 45%, var(--brand-green-light) 100%);
  }
</style>
</head>
<body>
  <section class="card card--front">
    <h1 class="front-name">Marlene Agate</h1>
    <p class="front-title">Commercial Loan Originator</p>
  </section>

  <section class="card card--back">
    <div class="portrait">
      <div class="portrait-fill" role="img" aria-label="Portrait photo of Marlene Agate"></div>
    </div>

    <div class="back-identity">
      <h2 class="back-name">Marlene Agate</h2>
      <div class="title-row">
        <p class="back-title">Commercial Loan Originator</p>
        <span class="title-rule"></span>
      </div>
    </div>

    <ul class="contact-list">
      <li class="contact-item">
        <svg class="contact-icon" viewBox="0 0 16 16" aria-hidden="true">
          <path d="M2 5c0-2 2.5-3 6-3s6 1 6 3v1.2h-3.2V4.8c-.8-.3-1.8-.4-2.8-.4s-2 .1-2.8.4v1.4H2z"/>
          <path d="M4.5 7h7l2 7h-11zM8 9a2 2 0 1 0 0 4 2 2 0 1 0 0-4z"/>
        </svg>
        <span>(800) 417-2906 x68</span>
      </li>
      <li class="contact-item">
        <svg class="contact-icon" viewBox="0 0 16 16" aria-hidden="true">
          <path d="M4.5 1h7a1 1 0 0 1 1 1v12a1 1 0 0 1-1 1h-7a1 1 0 0 1-1-1V2a1 1 0 0 1 1-1zm.6 1.8v9.4h5.8V2.8zM8 12.8a.7.7 0 1 0 0 1.4.7.7 0 1 0 0-1.4z"/>
        </svg>
        <span>(240) 615-2043</span>
      </li>
      <li class="contact-item">
        <svg class="contact-icon" viewBox="0 0 16 16" aria-hidden="true">
          <path d="M1 3.5h14v9H1zM2.2 4.7v.3L8 9l5.8-4v-.3z"/>
        </svg>
        <span>freshgreens4life@quillbox.example</span>
      </li>
    </ul>
  </section>
</body>
</html>
```